Crestline Plaque & Medal Unique Business Card Design

Recently selected a new logo design and waiting to recieve print files. I've attached image for your review. We are a trophies and awards company that provides engraving on trophies, plaques, name plates, name tags, desk sets, medals, acrylics, and signage.

We are located in Monroe, Louisiana and provide this service with computerized & laser engraving equipment.

Target Market(s)

Corporate, Sport, Church, and Special Events

Industry/Entity Type

Business

Contact Information for Business Card

I'd like to see the following list on the card: Trophies, Plaques, Name Plates, Name Tags, Desk Sets, Medals, Certificates... this is accomplished with Computerized & Laser Engraving

Colors
0555a3
ec1f27
ffffff

Requirements
Must have
• I like either single or double sided. If a design can be created with a frosted card stock I'd consider single. Must be Red, White, and Blue. Dwight Palmer - Owner, 412 W 8th Ave, Monroe, La 71208 office 318-555-0148 fax 318-555-0163 email: info@crestlineplaquemedal.example, and website: www.crestlineplaquemedal.example

```html
<!DOCTYPE html>
<html lang="en">
<head>
<meta charset="utf-8">
<title>Crestline Plaque &amp; Medal – Business Card</title>
<link href="https://fonts.googleapis.com/css2?family=Open+Sans:wght@400;600;700&display=swap" rel="stylesheet">
<style>
  :root {
    --brand-blue: #0555a3;
    --brand-red: #ec1f27;
    --paper: #ffffff;
    --ink: #1d1d1f;
    --backdrop: #e9e9ec;
  }
  * { box-sizing: border-box; margin: 0; padding: 0; }
  html, body { width: 1200px; height: 800px; overflow: hidden; }
  body {
    background: var(--backdrop);
    font-family: "Open Sans", Arial, sans-serif;
    position: relative;
  }
  .card {
    position: absolute;
    top: 250px;
    width: 520px;
    height: 300px;
    background: var(--paper);
    box-shadow: 0 6px 18px rgba(0,0,0,0.18);
    overflow: hidden;
  }
  .card--front { left: 50px; }
  .card--back { left: 630px; }
  .card__waves { position: absolute; inset: 0; width: 100%; height: 100%; }

  .brand {
    position: absolute;
    display: flex;
    align-items: center;
    gap: 8px;
    color: var(--brand-blue);
    font-weight: 700;
    white-space: nowrap;
  }
  .brand__dot {
    width: 12px; height: 12px; border-radius: 50%;
    background: var(--brand-red);
    flex: none;
  }
  .card--front .brand { top: 30px; right: 28px; font-size: 19px; }
  .card--back .brand { top: 80px; left: 0; right: 0; justify-content: center; font-size: 31px; }
  .card--back .brand__dot { width: 18px; height: 18px; }
  .brand__rule {
    position: absolute; height: 2px; background: var(--brand-blue);
  }
  .card--front .brand__rule { top: 62px; right: 28px; width: 250px; }
  .card--back .brand__rule { top: 134px; left: 70px; width: 380px; }

  .person { position: absolute; top: 28px; left: 26px; }
  .person__name { font-size: 20px; font-weight: 700; color: var(--ink); }
  .person__first { color: var(--brand-red); }
  .person__title { font-size: 11px; font-weight: 700; color: var(--ink); margin-top: 2px; }

  .contact {
    position: absolute; left: 26px;
    list-style: none;
    color: var(--paper);
    font-size: 11.5px;
    line-height: 20px;
  }
  .contact--phones { top: 128px; }
  .contact--online { top: 196px; }
  .contact__item { display: flex; align-items: center; gap: 8px; }
  .contact__icon { width: 11px; height: 11px; fill: var(--brand-red); flex: none; }
  .contact__item--plain { padding-left: 19px; }

  .products {
    position: absolute; top: 168px; left: 44px; right: 30px;
    color: var(--brand-blue);
    font-size: 12px; font-weight: 600; line-height: 20px;
  }
  .products__label { font-weight: 700; }
  .products__sep { color: var(--brand-red); padding: 0 4px; }
</style>
</head>
<body>

<section class="card card--front" aria-label="Business card front">
  <svg class="card__waves" viewBox="0 0 520 300" preserveAspectRatio="none" aria-hidden="true">
    <path d="M0,104 C140,84 220,244 360,234 C440,229 490,259 520,269 L520,300 L0,300 Z" fill="var(--brand-red)"/>
    <path d="M0,110 C140,90 220,250 360,240 C440,235 490,265 520,275 L520,300 L0,300 Z" fill="var(--brand-blue)"/>
  </svg>

  <div class="person">
    <p class="person__name"><span class="person__first">Dwight</span> Palmer</p>
    <p class="person__title">Owner</p>
  </div>

  <div class="brand"><span class="brand__dot"></span>Crestline Plaque &amp; Medal</div>
  <div class="brand__rule"></div>

  <ul class="contact contact--phones">
    <li class="contact__item">
      <svg class="contact__icon" viewBox="0 0 24 24" aria-hidden="true"><path d="M6.6 10.8a15.1 15.1 0 0 0 6.6 6.6l2.2-2.2a1 1 0 0 1 1-.25 11.4 11.4 0 0 0 3.6.57 1 1 0 0 1 1 1V20a1 1 0 0 1-1 1A17 17 0 0 1 3 4a1 1 0 0 1 1-1h3.5a1 1 0 0 1 1 1c0 1.25.2 2.45.57 3.57a1 1 0 0 1-.25 1z"/></svg>
      318-555-0148
    </li>
    <li class="contact__item">
      <svg class="contact__icon" viewBox="0 0 24 24" aria-hidden="true"><path d="M6 3h10v5H6zM4 9h16a2 2 0 0 1 2 2v6h-4v4H6v-4H2v-6a2 2 0 0 1 2-2zm4 7v3h8v-3z"/></svg>
      318-555-0163
    </li>
  </ul>

  <ul class="contact contact--online">
    <li class="contact__item">
      <svg class="contact__icon" viewBox="0 0 24 24" aria-hidden="true"><path d="M2 5h20v14H2zm2 2v.5l8 5 8-5V7z"/></svg>
      info@crestlineplaquemedal.example
    </li>
    <li class="contact__item">
      <svg class="contact__icon" viewBox="0 0 24 24" aria-hidden="true"><path d="M12 2a10 10 0 1 0 0 20 10 10 0 0 0 0-20zm0 2c1 1.3 1.8 3.4 2 6h-4c.2-2.6 1-4.7 2-6zM4.1 13h3.9c.1 2 .5 3.7 1.2 5A8 8 0 0 1 4.1 13zm0-2a8 8 0 0 1 5.1-6c-.7 1.3-1.1 3-1.2 6zm5.9 2h4c-.2 2.6-1 4.7-2 6-1-1.3-1.8-3.4-2-6zm6 0h3.9a8 8 0 0 1-5.1 5c.7-1.3 1.1-3 1.2-5zm0-2c-.1-3-.5-4.7-1.2-6a8 8 0 0 1 5.1 6z"/></svg>
      www.crestlineplaquemedal.example
    </li>
    <li class="contact__item contact__item--plain">412 W 8th Ave, Monroe, La 71208</li>
  </ul>
</section>

<section class="card card--back" aria-label="Business card back">
  <svg class="card__waves" viewBox="0 0 520 300" preserveAspectRatio="none" aria-hidden="true">
    <path d="M0,264 C150,250 300,296 520,278 L520,300 L0,300 Z" fill="var(--brand-red)"/>
    <path d="M0,270 C150,256 300,302 520,284 L520,300 L0,300 Z" fill="var(--brand-blue)"/>
  </svg>

  <div class="brand"><span class="brand__dot"></span>Crestline Plaque &amp; Medal</div>
  <div class="brand__rule"></div>

  <div class="products">
    <p class="products__label">Our Products:</p>
    <p>Trophies<span class="products__sep">|</span>Plaques<span class="products__sep">|</span>Name Plates<span class="products__sep">|</span>Name Tags<span class="products__sep">|</span>Desk Sets<span class="products__sep">|</span>Medals<span class="products__sep">|</span>Certificates...</p>
  </div>
</section>

</body>
</html>
```